New business card/stationary for a consulting company

I am looking for a clean and very professional looking business card for my consulting company as well as corresponding stationary. I am uploading our logo. I like simple and powerful for the feel. No graphics but I am open on everything else. Below is my contact information but would like the final to be in a version I can add my employees information into and print. Thank you.

Daniel Whitcombe
dan@ferncliffadvisory.com
2870 North 9th Avenue, Summit Floor, Elm Ridge, Illinois 60531
www.ferncliffadvisory.com

Industry/Entity Type

Consulting

Contact Information for Business Card

Daniel Whitcombe
dan@ferncliffadvisory.com
www.ferncliffadvisory.com

Font styles to use
Serif
Sans Serif

Requirements
Must have
• Our logo and the business card details.
Nice to have
• our website www.ferncliffadvisory.com

```html
<!DOCTYPE html>
<html lang="en">
<head>
<meta charset="utf-8">
<title>Ferncliff Advisory – Business Card</title>
<link rel="stylesheet" href="https://fonts.googleapis.com/css2?family=Questrial&family=Montserrat:wght@700&family=Roboto:wght@400;700&display=swap">
<style>
  :root {
    --navy: #05045f;
    --paper: #f6f6f6;
    --ink: #4a4a4a;
    --backdrop: #e4e2de;
    --silver: #e9e9ee;
  }
  * { margin: 0; padding: 0; box-sizing: border-box; }
  html, body { width: 1200px; height: 960px; overflow: hidden; }
  body { background: var(--backdrop); position: relative; font-family: "Roboto", sans-serif; }

  .card { position: absolute; width: 600px; height: 342px; box-shadow: 0 2px 6px rgba(0,0,0,.25); }
  .card--front { left: 302px; top: 129px; background: var(--paper); }
  .card--back  { left: 299px; top: 488px; height: 343px; background: var(--navy); }

  .brand-mark { position: absolute; width: 46px; height: 46px; }
  .brand-name { position: absolute; font-family: "Questrial", sans-serif; white-space: nowrap; letter-spacing: .04em; }

  .card--front .brand-mark { left: 152px; top: 42px; background: var(--navy); }
  .card--front .brand-name { left: 32px; width: 290px; text-align: center; top: 98px; font-size: 22px; color: var(--navy); }

  .contact { position: absolute; right: 40px; top: 206px; text-align: right; color: var(--ink); font-size: 14px; line-height: 18px; }
  .contact__name { font-family: "Montserrat", sans-serif; font-weight: 700; font-size: 19px; letter-spacing: .04em; color: var(--navy); line-height: 22px; }
  .contact__email { margin-bottom: 8px; }
  .contact__web { font-weight: 700; margin-top: 2px; letter-spacing: .02em; }
  .accent-bar { position: absolute; right: 2px; top: 209px; width: 10px; height: 99px; background: var(--navy); }

  .card--back .brand-mark { left: 270px; top: 117px; width: 60px; height: 60px; background: var(--silver); }
  .card--back .brand-name { left: 0; width: 600px; text-align: center; top: 194px; font-size: 31px; color: var(--silver); }
</style>
</head>
<body>
  <section class="card card--front">
    <div class="brand-mark"></div>
    <div class="brand-name">FERNCLIFF ADVISORY</div>
    <div class="contact">
      <p class="contact__name">DANIEL WHITCOMBE</p>
      <p class="contact__email">dan@ferncliffadvisory.com</p>
      <p>2870 North 9th Avenue</p>
      <p>Summit Floor, Elm Ridge, Illinois 60531</p>
      <p class="contact__web">FERNCLIFFADVISORY.COM</p>
    </div>
    <div class="accent-bar"></div>
  </section>

  <section class="card card--back">
    <div class="brand-mark"></div>
    <div class="brand-name">FERNCLIFF ADVISORY</div>
  </section>
</body>
</html>
```